Wordpress template for a mens-choire webpage

Task is to design a Wordpress template for an 98 years old estonian mens choire webpage.
Design should involve details from the attached files, choire logo and the colors of the choire flag: in horizontal orientation bright sky-blue, white, bright grass-green.
Designer signature is allowed to be added to the template, with country of origin.

Reason: Deadline extended 2 days (until 2. March 2014) to accommodate designers creativity.

Thank you everyone for your great designs!
Our project has now entered into a voting and decision phase until 14th of March 2014 (included).

```html
<!DOCTYPE html>
<html lang="en">
<head>
<meta charset="utf-8">
<title>Harbour Choir</title>
<link href="https://fonts.googleapis.com/css2?family=Lexend:wght@400;500&family=Ropa+Sans&family=Arimo:wght@400;700&display=swap" rel="stylesheet">
<style>
:root{
  --flag-green:#579d23;
  --flag-blue:#1f63a6;
  --nav-blue:#1ea4eb;
  --nav-active:#1890d2;
  --ink:#222;
  --body-text:#333;
  --muted:#888;
  --panel:#f4f4f4;
  --date-box:#555;
  --footer:#1c1c1c;
  --footer-text:#9a9a9a;
  --footer-head:#bdbdbd;
  --bottom-bar:#efefef;
}
*{margin:0;padding:0;box-sizing:border-box}
html,body{width:912px;height:1200px;overflow:hidden}
body{position:relative;background:#fff;font-family:'Arimo',sans-serif;color:var(--body-text)}
.backdrop{position:absolute;inset:0}
.page{position:absolute;left:130px;top:66px;width:652px;height:1052px;background:#fff}
.abs{position:absolute}
.brand{left:12px;top:30px;display:flex;align-items:center;gap:6px;font-family:'Ropa Sans',sans-serif;font-size:16px;color:#8a1c1c}
.brand .dot{width:12px;height:12px;border-radius:50%;background:#8a1c1c}
.contact{top:44px;font-size:8px;color:#222;display:flex;align-items:center;gap:7px;white-space:nowrap}
.contact .ic{width:19px;height:19px;border-radius:50%;background:#666;display:flex;align-items:center;justify-content:center}
.nav{left:0;top:105px;width:652px;height:31px;background:var(--nav-blue);display:flex;font-family:'Lexend',sans-serif;font-variant:small-caps;font-size:12px;letter-spacing:1px;color:#fff}
.nav a{color:#fff;text-decoration:none;display:flex;align-items:center;height:100%}
.nav .active{background:var(--nav-active)}
.hero{left:0;top:136px;width:652px;height:272px;background:linear-gradient(180deg,#1b1512 0%,#2a1d1a 45%,#3a2c2f 70%,#8a5a34 100%)}
.arrow{width:12px;height:22px;background:rgba(255,255,255,.35);display:flex;align-items:center;justify-content:center;top:134px}
.caption{left:178px;top:364px;width:338px;height:32px;background:rgba(255,255,255,.82);font-family:'Lexend',sans-serif;font-variant:small-caps;font-size:18px;letter-spacing:1px;color:#222;display:flex;align-items:center;justify-content:center}
.h{font-family:'Ropa Sans',sans-serif;font-size:12.5px;color:var(--ink)}
.intro{left:10px;top:466px;width:420px;font-size:7.4px;line-height:14.4px;color:#333;text-align:justify}
.rule{left:10px;top:552px;width:420px;height:1px;background:#eee}
.photo{display:block}
.tag{left:0;bottom:0;width:100%;height:24px;background:rgba(60,60,60,.75);color:#fff;font-family:'Ropa Sans',sans-serif;font-size:11px;display:flex;align-items:center;justify-content:center}
.overlay{inset:0;background:rgba(235,222,205,.6);display:flex;flex-direction:column;align-items:center;justify-content:center;text-align:center;font-family:'Ropa Sans',sans-serif;color:#222}
.overlay h4{font-weight:400;font-size:11.5px;margin-bottom:6px}
.overlay p{font-size:7px;line-height:14px}
.pager{font-size:9px;color:#888;letter-spacing:6px}
.events{left:449px;top:657px;width:194px;height:168px;background:var(--panel)}
.event{left:14px;width:172px;height:54px}
.date{left:0;top:0;width:29px;height:53px;background:var(--date-box);color:#fff;font-family:'Ropa Sans',sans-serif;font-size:10.5px;line-height:13px;display:flex;flex-direction:column;align-items:center;justify-content:center}
.event h5{position:absolute;left:58px;top:-1px;font-family:'Ropa Sans',sans-serif;font-weight:400;font-size:8.5px;color:#222}
.event p{position:absolute;left:58px;top:16px;width:120px;font-family:'Ropa Sans',sans-serif;font-size:7px;line-height:14.4px;color:#333;text-align:justify}
.dash{left:4px;top:83px;width:186px;border-top:1px dotted #999}
.footer{left:0;top:856px;width:652px;height:164px;background:var(--footer);color:var(--footer-text);font-size:7.6px}
.footer .fh{position:absolute;top:9px;font-size:11.5px;font-weight:700;color:var(--footer-head)}
.footer .frule{position:absolute;left:0;top:30px;width:652px;height:1px;background:#333}
.links{left:12px;top:41px;list-style:none;line-height:14.4px}
.links li::before{content:"•";margin-right:20px}
.social{left:12px;top:116px;display:flex;gap:6px}
.social span{width:16px;height:16px;border-radius:50%;background:#bdbdbd}
.tweet{left:207px;width:230px;line-height:14.4px}
.tweet .bullet{position:absolute;left:-30px;top:2px;width:10px;height:10px;border-radius:50%;background:#eee}
.touch{left:489px;line-height:14.4px;white-space:nowrap}
.touch .ic{position:absolute;left:-20px;top:2px;width:9px;height:9px}
.bottom{left:0;top:1020px;width:652px;height:32px;background:var(--bottom-bar);font-size:7.6px;color:#222;display:flex;align-items:center;justify-content:center}
.bottom span{color:#888;margin:0 3px}
</style>
</head>
<body>
<svg class="backdrop" width="912" height="1200" viewBox="0 0 912 1200" aria-hidden="true">
  <polygon points="0,0 912,0 912,160 0,396" fill="var(--flag-green)"/>
  <polygon points="0,848 912,560 912,1200 0,1200" fill="var(--flag-blue)"/>
</svg>

<div class="page">
  <header>
    <div class="abs brand"><span class="dot"></span>Harbour Choir</div>
    <div class="abs contact" style="left:403px">
      <span class="ic"><svg width="10" height="10" viewBox="0 0 10 10"><path d="M2 1l2 2-1 1c1 1.5 1.5 2 3 3l1-1 2 2-1.5 1.5C4 9 1 6 .5 2.5z" fill="#fff"/></svg></span>Call Us : 1800-5550-0142
    </div>
    <div class="abs contact" style="left:536px">
      <span class="ic"><svg width="10" height="8" viewBox="0 0 10 8"><rect x=".5" y=".5" width="9" height="7" fill="none" stroke="#fff"/><path d="M.5 .5L5 4.5 9.5.5" fill="none" stroke="#fff"/></svg></span>info@harbourchoir.org
    </div>
    <nav class="abs nav">
      <a class="active" style="width:72px;padding-left:23px">Home</a>
      <a style="margin-left:13px">Blog</a>
      <a style="margin-left:28px">Events</a>
      <a style="margin-left:28px">Artist</a>
      <a style="margin-left:28px">Albums</a>
      <a style="margin-left:28px">Videos</a>
      <a style="margin-left:28px">News</a>
      <a style="margin-left:46px">Contact Us</a>
    </nav>
  </header>

  <section class="abs hero" role="img" aria-label="Photo of a men's choir in striped blazers singing on stage before a seated audience"></section>
  <div class="abs arrow" style="left:0"><svg width="6" height="8"><path d="M5 0L1 4l4 4" stroke="#fff" fill="none" stroke-width="1.5"/></svg></div>
  <div class="abs arrow" style="left:640px"><svg width="6" height="8"><path d="M1 0l4 4-4 4" stroke="#fff" fill="none" stroke-width="1.5"/></svg></div>
  <div class="abs caption">98 Years of Estonian Choire</div>

  <h2 class="abs h" style="left:10px;top:440px;font-weight:400">Welcome To Our Company</h2>
  <p class="abs intro">Lorem ipsum dolor sit amet, consectetur adipiscing elit. Nulla blandit tempus malesuada. Nam quis orci quis nibh viverra imperdiet vel sit amet mauris.Lorem ipsum dolor sit amet, consectetur adipiscing elit. Nulla blandit tempus malesuada. Nam quis orci quis nibh viverra imperdiet vel sit amet mauris. Quisque pretium purus luctus tortor volutpat ac suscipit turpis condimentum.Even the all-powerful Pointing has no control about the blind texts it is an almost unorthographic life One day however a small line of blind text by the name of Lorem Ipsum decided to leave for the far</p>
  <div class="abs rule"></div>

  <h2 class="abs h" style="left:10px;top:572px;font-weight:400">Latest Articles</h2>
  <article class="abs" style="left:11px;top:596px;width:198px;height:230px">
    <div class="photo abs" style="inset:0;background:linear-gradient(180deg,#8c949c 0%,#b9c2c9 40%,#2a2a2c 70%,#1d1d1f 100%)" role="img" aria-label="Photo of a line of singers in black tuxedos by the sea"></div>
    <div class="abs tag">Harbour Male Voices</div>
  </article>
  <article class="abs" style="left:232px;top:596px;width:198px;height:230px">
    <div class="photo abs" style="inset:0;background:linear-gradient(160deg,#c79a6a 0%,#5c4a3e 50%,#8a7a6a 100%)" role="img" aria-label="Photo of choir singers holding song folders"></div>
    <div class="abs overlay">
      <h4>Mauris eget commodo velit</h4>
      <p>Sat 18 Jun 2012 // mark olsen, interview<br>we love building awesome products on the web.<br>We love it so much, we decided to</p>
    </div>
  </article>

  <h2 class="abs h" style="left:449px;top:440px;font-weight:400">Latest Videos</h2>
  <div class="abs pager" style="left:625px;top:443px">‹ ›</div>
  <div class="abs" style="left:449px;top:462px;width:194px;height:154px;background:linear-gradient(180deg,#c8b49a 0%,#6a4a3a 40%,#3a2c2c 80%,#111 100%)" role="img" aria-label="Video still of a mixed choir performing in a concert hall"></div>
  <svg class="abs" style="left:529px;top:520px" width="38" height="38" viewBox="0 0 38 38" aria-hidden="true"><circle cx="19" cy="19" r="18" fill="rgba(60,60,60,.6)"/><path d="M15 12l11 7-11 7z" fill="#fff"/></svg>
  <div class="abs" style="left:449px;top:604px;width:194px;height:12px;background:#151515"></div>
  <div class="abs" style="left:449px;top:604px;width:194px;height:2px;background:#555"></div>

  <h2 class="abs h" style="left:449px;top:635px;font-weight:400">Upcoming Events</h2>
  <div class="abs pager" style="left:625px;top:638px">‹ ›</div>
  <section class="abs events">
    <div class="abs event" style="top:19px">
      <div class="abs date"><span>24</span><span>AUG</span></div>
      <h5>SILVER PINES LIVE</h5>
      <p>Lorem ipsum dolor sit amet, consectetur adipisicing elit, sed do eiusmod tempor</p>
    </div>
    <div class="abs dash"></div>
    <div class="abs event" style="top:99px">
      <div class="abs date"><span>24</span><span>AUG</span></div>
      <h5>KETTLE DRUM CLUB</h5>
      <p>Lorem ipsum dolor sit amet, consectetur adipisicing elit, sed do eiusmod tempor</p>
    </div>
  </section>

  <footer class="abs footer">
    <h3 class="fh" style="left:12px">Browse around</h3>
    <h3 class="fh" style="left:177px">Latest tweet</h3>
    <h3 class="fh" style="left:469px">Get in Touch</h3>
    <div class="frule"></div>
    <ul class="abs links"><li>Home</li><li>News</li><li>Events</li><li>Artists</li></ul>
    <div class="abs social"><span></span><span></span><span></span><span></span></div>
    <div class="abs tweet" style="top:41px"><span class="bullet"></span>@linamortensen thanks for your feedback lina, we're working on improving our payment process and making our site easier to use. ^ca</div>
    <div class="abs tweet" style="top:89px"><span class="bullet"></span>@linamortensen thanks for your feedback lina, we're working on improving our payment process and making our site easier to use. ^ca</div>
    <div class="abs touch" style="top:44px"><svg class="ic" viewBox="0 0 10 10"><path d="M2 1l2 2-1 1c1 1.5 1.5 2 3 3l1-1 2 2-1.5 1.5C4 9 1 6 .5 2.5z" fill="#888"/></svg>(800) 555-0187</div>
    <div class="abs touch" style="top:64px">517-555-0123</div>
    <div class="abs touch" style="top:89px"><svg class="ic" viewBox="0 0 10 8"><rect x=".5" y=".5" width="9" height="7" fill="none" stroke="#888"/><path d="M.5 .5L5 4.5 9.5.5" fill="none" stroke="#888"/></svg>info@harbourchoir.org</div>
    <div class="abs touch" style="top:110px"><svg class="ic" viewBox="0 0 10 10"><circle cx="5" cy="5" r="4.5" fill="#888"/></svg>http://harbourchoir.org/</div>
    <div class="abs touch" style="top:130px"><svg class="ic" viewBox="0 0 10 12"><path d="M5 12C2 8 .5 6 .5 4.5a4.5 4.5 0 019 0C9.5 6 8 8 5 12z" fill="#888"/></svg>Maple Hall, 120 Harbour Lane,<br>&nbsp;Suite 4 Riverton,</div>
  </footer>
  <div class="abs bottom">© 2014 <span>harbourchoir.org</span>. All rights reserved.</div>
</div>
</body>
</html>
```